Direct to Consumer extended service contract business with a new disruptive business model needs a

We need a customized wordpress design for a company called 'Bright Harbor Assurance'.
We provide an innovative and unique service contract protection program direct to consumers. This program provides monthly coverage for all electronics purchased in the last 4 years and all electronics the consumer purchases in the future for a low monthly fee. The overall design should communicate a sense of legitimacy, ethics, and superior customer service and support (in an industry that has a huge PR issue to overcome).
Electronics is the first product group, other product groups with different price points to launch in the future..

Target Market(s)

All purchasers of electronic goods...all demographics

Industry/Entity Type

Electronics

Font styles to use
Sans Serif

Requirements
Must have
• Customer Testimonials
Industry News
Customer ratings
Blog posts
Call to action messaging
Like the functional elements and design of quillmesa.example (need to be better)
Nice to have
• Like to see video testimonials
Social network "whats trending related to electronics or service contract industry"
Easy way to register products for warranty

```html
<!DOCTYPE html>
<html lang="en">
<head>
<meta charset="utf-8">
<title>Bright Harbor Assurance – Homepage Layout</title>
<link rel="stylesheet" href="https://fonts.googleapis.com/css2?family=Mulish:wght@400;600;700;800&family=Pathway+Gothic+One&display=swap">
<style>
:root{
  --green:#3a9e1e;
  --green-text:#2db35a;
  --blue-nav:#2f5ba8;
  --blue-logo:#1aa0e0;
  --blue-head:#2aa3d8;
  --blue-text:#2e5fae;
  --grey-band:#e6e6e6;
  --grey-text:#555;
  --dark:#333;
  --fb:#3b5ea0;
  --tw:#3ab0e2;
  --yt:#e01010;
  --note:#1a1a1a;
}
*{box-sizing:border-box;margin:0;padding:0}
html,body{width:960px;height:1200px;overflow:hidden;background:#fff}
body{font-family:'Mulish',sans-serif;color:var(--dark)}
.stage{position:absolute;left:0;top:0;width:1200px;height:1500px;transform:scale(.8);transform-origin:0 0}
.abs{position:absolute}

.note{position:absolute;font-family:'Pathway Gothic One',sans-serif;font-size:24px;line-height:30px;color:var(--note)}
.brackets{position:absolute;left:0;top:0}

.page{position:absolute;left:254px;top:0;width:692px;height:1500px;background:#fff}
.topbar{position:absolute;left:0;top:0;width:692px;height:18px;background:linear-gradient(#4caf22,var(--green));color:#fff;font-size:8px;font-weight:700;text-align:right;padding:5px 6px 0 0;letter-spacing:.2px}
.header{position:absolute;left:0;top:18px;width:692px;height:56px;background:#fff}
.brand{position:absolute;left:21px;top:18px;font-size:19px;font-weight:800;color:var(--blue-logo)}
.main-nav{position:absolute;right:26px;top:22px;display:flex;gap:22px;font-size:13px;color:var(--dark)}
.cat-nav{position:absolute;left:0;top:74px;width:692px;height:33px;background:var(--blue-nav);display:flex;justify-content:space-around;align-items:center;padding:0 6px;color:#fff;font-size:11px;font-weight:700}

.hero{position:absolute;left:0;top:107px;width:692px;height:290px;background:linear-gradient(#d6d6d6,#f6f6f6 80%,#fff)}
.hero-title{position:absolute;left:0;top:18px;width:692px;text-align:center;color:var(--blue-head);font-size:23px;line-height:21px;font-weight:600}
.devices{position:absolute;left:48px;top:73px;width:228px;height:210px;border-radius:6px;background:linear-gradient(135deg,#3a3a3a,#6c8fb4 45%,#e7eef5)}
.quote-box{position:absolute;left:329px;top:75px;width:338px;height:190px;background:#fff;box-shadow:0 0 2px rgba(0,0,0,.12)}
.quote-box h2{position:absolute;left:0;top:10px;width:338px;text-align:center;color:var(--green-text);font-size:22px;font-weight:600}
.select{position:absolute;left:18px;width:302px;height:34px;border:1px solid #e3e3e3;color:var(--blue-text);font-size:15px;padding:7px 10px}
.select svg{position:absolute;right:9px;top:12px}
.btn-quote{position:absolute;left:20px;top:131px;width:298px;height:33px;background:linear-gradient(#3bb024,#2b9a18);color:#fff;font-size:21px;font-weight:600;text-align:center;line-height:33px}

.band{position:absolute;left:0;width:692px}
.section-title{position:absolute;left:0;width:692px;text-align:center;font-size:19px;font-weight:400;letter-spacing:1px;color:var(--grey-text)}

.ratings{top:397px;height:181px;background:var(--grey-band)}
.rating-strip{position:absolute;left:34px;top:65px;width:624px;height:94px;background:#fff}
.rating{position:absolute;top:18px;width:200px;height:60px}
.rating .badge{position:absolute;left:0;top:2px;width:58px;height:58px;border-radius:50%}
.rating h3{position:absolute;left:63px;top:-4px;font-size:17px;font-weight:600;color:#222}
.rating p{position:absolute;left:63px;top:17px;width:120px;font-size:10px;line-height:14px;color:#444}
.rating .stars{position:absolute;left:61px;top:44px}
.arrow{position:absolute}

.blog{top:578px;height:240px;background:linear-gradient(#f9f9f9,#fff 20%,#fff 85%,#f1f1f1)}
.post{position:absolute;top:60px;width:180px;height:146px;background:#f5f5f5}
.post .thumb{width:180px;height:100px;background:linear-gradient(135deg,#2fae5f,#5fc787)}
.post p{padding:5px 9px;font-size:13px;line-height:17px;color:var(--green-text)}

.feature{top:818px;height:322px;background:var(--grey-band)}
.panel{position:absolute;top:32px;width:306px;height:268px;background:#fff}
.panel h2{position:absolute;left:0;top:8px;width:306px;text-align:center;color:var(--green-text);font-size:22px;font-weight:600}
.news-item{position:absolute;left:10px;width:287px;height:46px;background:#f3f3f3;border:1px solid #e6e6e6}
.news-item .thumb{position:absolute;left:3px;top:4px;width:62px;height:38px;background:var(--blue-nav)}
.news-item p{position:absolute;left:75px;top:3px;width:205px;font-size:10px;line-height:13px;color:var(--green-text)}
.news-item time{position:absolute;left:75px;top:32px;font-size:8px;color:#555}
.video-main{position:absolute;left:14px;top:41px;width:276px;height:152px;background:radial-gradient(circle at 60% 40%,#2f5a98,#123066 75%)}
.video-thumb{position:absolute;top:201px;width:91px;height:50px;background:radial-gradient(circle at 60% 40%,#2f5a98,#123066 80%)}
.play{position:absolute}

.social{top:1140px;height:300px;background:var(--grey-band)}
.feed{position:absolute;top:70px;width:194px;height:202px;background:#fff;border:1px solid #ddd}
.feed-head{height:26px;color:#fff;font-size:13px;font-weight:700;padding:4px 11px}
.fb-head{background:linear-gradient(#4f73b6,var(--fb))}
.tw-head{background:linear-gradient(#5fc7ee,var(--tw))}
.yt-head{background:linear-gradient(#f02a2a,var(--yt))}
.tiny{font-size:6px;line-height:8px;color:#444}
.fb-grid{position:absolute;left:15px;top:101px;display:grid;grid-template-columns:repeat(5,29px);gap:3px}
.fb-grid span{width:29px;height:28px;background:var(--blue-nav)}
.tweet{position:absolute;left:6px;width:182px;height:28px;border-bottom:1px solid #eee}
.tweet .av{position:absolute;left:0;top:2px;width:17px;height:17px;background:#b5a48f}
.tweet .tiny{position:absolute;left:22px;top:1px;width:160px}
.tweet b{color:#222}

.footer{position:absolute;left:0;top:1440px;width:692px;height:60px;background:var(--blue-nav);color:#fff;text-align:center;font-size:8px;font-weight:700;padding-top:18px;line-height:15px}
</style>
</head>
<body>
<div class="stage">

  <div class="note" style="left:25px;top:22px">header with logo<br>and menu according<br>to the site req</div>
  <div class="note" style="left:22px;top:443px">auto scroll customer<br>raiting with stars</div>
  <div class="note" style="left:29px;top:913px">Industial news with<br>thumbnail, date and<br>heading</div>
  <div class="note" style="left:33px;top:1239px">Social media/network<br>feed with website's<br>official accounts</div>
  <div class="note" style="left:1012px;top:231px">Call to action<br>messaging</div>
  <div class="note" style="left:1015px;top:623px">Latest blog posts<br>with thumbnail &amp;<br>heading of post</div>
  <div class="note" style="left:1017px;top:920px">Video testimonials<br>with feature and<br>three other videos</div>
  <div class="note" style="left:987px;top:1458px;font-size:20px">footer with all links/ detail</div>

  <svg class="brackets" width="1200" height="1500" aria-hidden="true">
    <g fill="none" stroke="#111" stroke-width="1.6">
      <path d="M244 14H224V94H244M192 53H224"/>
      <path d="M244 414H224V546H244M192 479H224"/>
      <path d="M244 869H222V1097H244M190 980H222"/>
      <path d="M244 1189H222V1417H244M190 1300H222"/>
      <path d="M955 156H970V378H955M970 264H996"/>
      <path d="M958 619H973V751H958M973 684H998"/>
      <path d="M958 868H973V1097H958M973 980H998"/>
      <path d="M955 1455H973V1495H955M973 1472H986"/>
    </g>
  </svg>

  <div class="page">
    <div class="topbar">LOGIN - REGISTER - SUPPORT / CALL: 001-555-0199</div>

    <header class="header">
      <div class="brand">Bright Harbor Assurance</div>
      <nav class="main-nav"><span>HOME</span><span>ABOUT</span><span>BLOG</span><span>NEWS</span><span>CLIENTS</span></nav>
    </header>

    <nav class="cat-nav">
      <span>MOBILES</span><span>SLATES</span><span>LAPTOPS</span><span>TABLETS</span><span>EREADERS</span><span>SMARTPHONES</span><span>CAMERAS</span><span>TELEVISIONS</span><span>ALL PRODUCTS</span>
    </nav>

    <section class="hero">
      <h1 class="hero-title">“PAY LESS AND CLAIM MORE ON YOUR<br>ELECTRONIC DEVICE INSURANCE”</h1>
      <div class="devices" role="img" aria-label="Desktop monitor, tablet and phone showing a website"></div>
      <div class="quote-box">
        <h2>GET A QUOTE TODAY</h2>
        <div class="select" style="top:43px">Select your mobile phone
          <svg width="14" height="8"><path d="M0 0H14L7 8Z" fill="#2e5fae"/></svg></div>
        <div class="select" style="top:84px">Select service provider
          <svg width="14" height="8"><path d="M0 0H14L7 8Z" fill="#2e5fae"/></svg></div>
        <div class="btn-quote">GET QUOTE</div>
      </div>
    </section>

    <section class="band ratings">
      <h2 class="section-title" style="top:29px">CUSTOMER RAITING</h2>
      <svg class="arrow" style="left:19px;top:102px" width="11" height="20"><path d="M11 0V20L0 10Z" fill="#222"/></svg>
      <svg class="arrow" style="left:663px;top:102px" width="11" height="20"><path d="M0 0V20L11 10Z" fill="#222"/></svg>
      <div class="rating-strip">
        <div class="rating" style="left:12px">
          <div class="badge" style="background:#3a3a3a"></div>
          <h3>Orchard Store</h3><p>some info came here with description.</p>
          <svg class="stars" width="110" height="16"><g fill="#e8372a"><use href="#star" x="0"/><use href="#star" x="21"/><use href="#star" x="42"/><use href="#star" x="63"/><use href="#star" x="84"/></g></svg>
        </div>
        <div class="rating" style="left:214px">
          <div class="badge" style="background:#2a2a2a"></div>
          <h3>Riverline Store</h3><p>some info came here with description.</p>
          <svg class="stars" width="110" height="16"><g fill="#2e7fd8"><use href="#star" x="0"/><use href="#star" x="21"/><use href="#star" x="42"/><use href="#star" x="63"/><use href="#star" x="84"/></g></svg>
        </div>
        <div class="rating" style="left:423px">
          <div class="badge" style="background:#e0392c"></div>
          <h3>Searchly Store</h3><p>some info came here with description.</p>
          <svg class="stars" width="110" height="16"><g fill="#6cbf2a"><use href="#star" x="0"/><use href="#star" x="21"/><use href="#star" x="42"/><use href="#star" x="63"/><use href="#star" x="84"/></g></svg>
        </div>
      </div>
      <svg width="0" height="0"><defs><path id="star" d="M8 0L10 5.6H16L11.2 9.2L13 15L8 11.5L3 15L4.8 9.2L0 5.6H6Z"/></defs></svg>
    </section>

    <section class="band blog">
      <h2 class="section-title" style="top:18px">LATEST BLOG POSTS</h2>
      <article class="post" style="left:39px"><div class="thumb" role="img" aria-label="Blog post thumbnail"></div><p>Lorem ipsum nipsum saye losamu</p></article>
      <article class="post" style="left:257px"><div class="thumb" role="img" aria-label="Blog post thumbnail"></div><p>Lorem ipsum nipsum saye losamu</p></article>
      <article class="post" style="left:474px"><div class="thumb" role="img" aria-label="Blog post thumbnail"></div><p>Lorem ipsum nipsum saye losamu</p></article>
    </section>

    <section class="band feature">
      <div class="panel" style="left:34px">
        <h2>INDUSTRIAL NEWS</h2>
        <div class="news-item" style="top:50px"><div class="thumb"></div><p>Lorem ipsum nipsum saye losamu this kird yua. Heading of news.</p><time>Date: 10-20-2015</time></div>
        <div class="news-item" style="top:102px"><div class="thumb"></div><p>Lorem ipsum nipsum saye losamu this kird yua. Heading of news.</p><time>Date: 10-20-2015</time></div>
        <div class="news-item" style="top:154px"><div class="thumb"></div><p>Lorem ipsum nipsum saye losamu this kird yua. Heading of news.</p><time>Date: 10-20-2015</time></div>
        <div class="news-item" style="top:206px"><div class="thumb"></div><p>Lorem ipsum nipsum saye losamu this kird yua. Heading of news.</p><time>Date: 10-20-2015</time></div>
      </div>
      <div class="panel" style="left:351px">
        <h2>TESTIMONIALS</h2>
        <div class="video-main" role="img" aria-label="Featured customer video testimonial"></div>
        <svg class="play" style="left:130px;top:95px" width="44" height="44"><circle cx="22" cy="22" r="22" fill="#56b92c"/><path d="M16 12V32L33 22Z" fill="#fff"/></svg>
        <div class="video-thumb" style="left:14px" role="img" aria-label="Video testimonial thumbnail"></div>
        <div class="video-thumb" style="left:106px" role="img" aria-label="Video testimonial thumbnail"></div>
        <div class="video-thumb" style="left:198px" role="img" aria-label="Video testimonial thumbnail"></div>
        <svg class="play" style="left:52px;top:220px" width="13" height="13"><circle cx="6.5" cy="6.5" r="6.5" fill="#56b92c"/><path d="M5 3.5V9.5L10 6.5Z" fill="#fff"/></svg>
        <svg class="play" style="left:144px;top:220px" width="13" height="13"><circle cx="6.5" cy="6.5" r="6.5" fill="#56b92c"/><path d="M5 3.5V9.5L10 6.5Z" fill="#fff"/></svg>
        <svg class="play" style="left:236px;top:220px" width="13" height="13"><circle cx="6.5" cy="6.5" r="6.5" fill="#56b92c"/><path d="M5 3.5V9.5L10 6.5Z" fill="#fff"/></svg>
      </div>
    </section>

    <section class="band social">
      <h2 class="section-title" style="top:30px">LATEST FROM SOCIAL MEDIA</h2>

      <div class="feed" style="left:34px">
        <div class="feed-head fb-head">Like us on Circlebook</div>
        <div class="abs" style="left:15px;top:47px;width:27px;height:27px;background:var(--blue-nav)"></div>
        <div class="abs tiny" style="left:49px;top:51px;color:var(--blue-nav);font-size:7px">Bright Harbor Assurance</div>
        <div class="abs tiny" style="left:49px;top:62px;background:var(--blue-nav);color:#fff;padding:0 3px">Like</div>
        <div class="abs tiny" style="left:15px;top:88px">3,249,061 people like Bright Harbor Assurance.</div>
        <div class="fb-grid"><span></span><span></span><span></span><span></span><span></span><span></span><span></span><span></span><span></span><span></span></div>
        <div class="abs tiny" style="left:15px;top:170px;color:#888">Circlebook social plugin</div>
      </div>

      <div class="feed" style="left:248px">
        <div class="feed-head tw-head">Latest from Chirpline</div>
        <div class="tweet" style="top:40px"><div class="av"></div><div class="tiny"><b>quillfan</b><br>Got my tablet fixed in two days, great<br>2 hours ago</div></div>
        <div class="tweet" style="top:70px"><div class="av"></div><div class="tiny"><b>techmom22</b><br>Screen claim done without a single call<br>2 hours ago</div></div>
        <div class="tweet" style="top:100px"><div class="av"></div><div class="tiny"><b>dailygadget</b><br>Monthly plan covers all my old devices<br>2 hours ago</div></div>
        <div class="tweet" style="top:130px"><div class="av"></div><div class="tiny"><b>homeoffice</b><br>Laptop died, replacement came fast and easy today<br>2 hours ago</div></div>
        <div class="tweet" style="top:163px;border:0"><div class="av"></div><div class="tiny"><b>rivercam</b><br>Finally a warranty company that answers the phone<br>2 hours ago</div></div>
      </div>

      <div class="feed" style="left:464px">
        <div class="feed-head yt-head">Join us on Streamly</div>
        <div class="abs" style="left:11px;top:36px;width:34px;height:28px;background:var(--blue-nav)"></div>
        <div class="abs tiny" style="left:54px;top:37px;font-size:7px">Bright Harbor Assurance</div>
        <div class="abs tiny" style="left:54px;top:49px;background:var(--yt);color:#fff;padding:1px 4px;font-weight:700">Subscribe</div>
        <div class="abs" style="left:8px;top:72px;width:177px;height:118px;background:linear-gradient(#1c1c1c,#4a4a4a)" role="img" aria-label="Embedded channel video"></div>
        <svg class="abs" style="left:82px;top:104px" width="38" height="42"><path d="M0 0V42L38 21Z" fill="#3a7bd5"/></svg>
        <svg class="abs" style="left:10px;top:180px" width="173" height="8"><rect x="0" y="3" width="173" height="2" fill="#777"/><rect x="10" y="3" width="100" height="2" fill="#ddd"/><rect x="140" y="3" width="25" height="2" fill="#ddd"/></svg>
      </div>
    </section>

    <footer class="footer">
      Home | About Us | Plans | Services | Benefits | Support | Contact Us<br>
      Copyright © 2014 Bright Harbor Assurance
    </footer>
  </div>
</div>
</body>
</html>
```